A private security company called "Tavron Security Services Ltd"

Hello everybody,

We need a web page for a company based in NZ. It is mainly an informative website so it would be wonderful if the designer puts their absolute best into making it a website that I would really appreciate. The website needs to show professionalism and also needs to make our web surfers find the information they need in a click. the company's colour is black and silver, and if those two colours could be integrated into the website it would be absolutely lovely. Please do contact me for any information.

Sincerely,
Dorian Vaskel

Industry/Entity Type

Security

```html
<!DOCTYPE html>
<html lang="en">
<head>
<meta charset="utf-8">
<title>Tavron Security Services Ltd</title>
<link href="https://fonts.googleapis.com/css2?family=Archivo+Narrow:wght@400;500;600&family=Arimo:wght@400;700&display=swap" rel="stylesheet">
<style>
:root{
  --ink:#1c1c1c;
  --text:#555;
  --muted:#8a8a8a;
  --silver-1:#ffffff;
  --silver-2:#e6e6e6;
  --silver-3:#d2d2d2;
  --line:#cfcfcf;
  --dark-1:#555555;
  --dark-2:#2b2b2b;
  --dark-3:#1e1e1e;
  --icon:#9a9a9a;
}
*{box-sizing:border-box;margin:0;padding:0}
html,body{width:1200px;height:2752px;overflow:hidden}
body{position:relative;font-family:"Arimo",Arial,sans-serif;color:var(--text);background:#fff}
.abs{position:absolute}
.head{font-family:"Archivo Narrow","Arial Narrow",sans-serif;font-weight:500;color:var(--ink);white-space:nowrap}

/* header */
.site-header{left:0;top:0;width:1200px;height:158px;background:linear-gradient(#fff,var(--silver-2));border-bottom:1px solid #c8c8c8}
.brand{left:157px;top:58px;display:flex;align-items:center;gap:12px}
.brand-dot{width:30px;height:30px;border-radius:50%;background:#2a2a2a}
.brand-name{font-family:"Archivo Narrow","Arial Narrow",sans-serif;font-weight:600;font-size:22px;color:#222;letter-spacing:.5px;line-height:1.05}
.main-nav{top:98px;font-size:13px;color:#222;letter-spacing:.3px}
.social{display:flex;gap:8px}
.social span{width:32px;height:32px;border-radius:50%;background:var(--icon);display:block}
.header-social{left:932px;top:30px}

/* hero */
.hero{left:0;top:158px;width:1200px;height:517px;background:radial-gradient(ellipse at 35% 40%,var(--dark-1),var(--dark-2) 75%)}
.hero-arrow{width:52px;height:52px;border-radius:50%;background:rgba(90,90,90,.85);top:233px}
.hero-title{z-index:2;left:216px;top:222px;font-family:"Archivo Narrow","Arial Narrow",sans-serif;font-size:31px;line-height:45px;color:#e8e8e8;font-weight:400;letter-spacing:-.2px;white-space:nowrap}
.hero-title strong{font-weight:600;color:#fff}
.hero-photo{left:790px;top:58px;width:170px;height:459px;background:linear-gradient(90deg,#6e6e6e,#d9d9d9 45%,#8a8a8a);border-radius:4px}

/* solutions */
.solutions{left:0;top:675px;width:1200px;height:712px;background:linear-gradient(#f6f6f6,#dcdcdc)}
.section-title{width:1200px;left:0;text-align:center;font-size:38px}
.services-heading{left:157px;top:152px;font-size:22px}
.services-list{left:157px;top:210px;list-style:none;width:210px}
.services-list li{position:relative;padding-left:32px;font-size:12px;line-height:16px;color:#777;margin-bottom:21px}
.services-list li::before{content:"";position:absolute;left:6px;top:1px;width:14px;height:14px;border-radius:50%;background:#d8d8d8}
.custom-box{left:157px;top:423px;width:211px;height:252px;background:linear-gradient(#8c8c8c,#e6e6e6 55%,#9a9a9a);text-align:center;padding-top:30px}
.custom-box .head{font-size:23px;line-height:33px;color:#3a3a3a}
.custom-box .box-name{margin-top:60px;font-family:"Archivo Narrow","Arial Narrow",sans-serif;font-weight:600;font-size:17px;color:#222}
.col-line{width:1px;top:151px;height:561px;background:var(--line)}
.row-line{height:1px;background:var(--line)}
.card{padding:4px 14px 0}
.card-img{height:100px;border:4px solid #fff;box-shadow:0 1px 3px rgba(0,0,0,.25)}
.card h3{font-size:18px;margin-top:18px;letter-spacing:-.2px}
.card p{font-size:11px;line-height:14px;color:#888;margin-top:6px}
.btn{display:inline-block;border:1px solid #bbb;border-radius:3px;background:linear-gradient(#fff,#dedede);color:#333;font-size:11px;padding:6px 9px;white-space:nowrap}
.card .btn{position:absolute;right:16px}

/* industries */
.industries{left:0;top:1387px;width:1200px;height:403px;background:#fff}
.ind-item{top:145px;width:196px;text-align:center}
.ind-img{height:158px;border:4px solid #eee;box-shadow:0 1px 3px rgba(0,0,0,.2)}
.ind-item .head{font-size:18px;margin-top:14px;letter-spacing:-.2px}
.ind-arrow{width:36px;height:36px;border-radius:50%;background:#aaa;top:204px}

/* solutions split */
.split{left:0;top:1790px;width:1200px;height:482px;background:linear-gradient(#f3f3f3,#ececec)}
.split-divider{left:600px;top:60px;width:1px;height:360px;background:linear-gradient(transparent,#cfcfcf,transparent)}
.split-col{top:79px;width:420px;text-align:center}
.split-img{width:176px;height:176px;border-radius:50%;margin:0 auto;border:8px solid #e2e2e2;box-shadow:0 2px 4px rgba(0,0,0,.15)}
.split-col .head{font-size:19px;margin-top:18px}
.split-col p{font-size:11.5px;line-height:15px;color:#999;margin:12px auto 0;width:360px}
.split-col .btn{margin-top:20px;padding:7px 22px}

/* footer */
.site-footer{left:0;top:2272px;width:1200px;height:480px;background:radial-gradient(ellipse at 50% 0%,#5a5a5a,var(--dark-2) 70%,var(--dark-3))}
.footer-title{font-family:"Archivo Narrow","Arial Narrow",sans-serif;font-size:28px;color:#eee;top:60px;white-space:nowrap}
.about-text{left:157px;top:128px;width:305px;font-size:11px;line-height:14px;color:#777}
.about-text p+p{margin-top:14px}
.quick-links{left:541px;top:128px;list-style:none}
.quick-links li{font-size:11px;color:#888;line-height:14px;margin-bottom:17.5px;padding-left:20px;position:relative;letter-spacing:.3px}
.quick-links svg{position:absolute;left:0;top:2px}
.news-text{left:769px;top:128px;width:280px;font-size:11px;line-height:14px;color:#777}
.field{left:769px;width:274px;height:33px;background:#5a5a5a;border:1px solid #666;color:#ccc;font-size:11px;padding:9px 20px}
.footer-rule{left:157px;top:388px;width:886px;height:1px;background:#3e3e3e;box-shadow:0 1px 0 #4d4d4d}
.copyright{left:157px;top:425px;font-size:11px;color:#888}
.footer-social{left:932px;top:415px}
</style>
</head>
<body>

<header class="abs site-header">
  <div class="abs brand"><span class="brand-dot"></span><span class="brand-name">TAVRON<br><span style="font-size:13px">Security Services Ltd.</span></span></div>
  <nav>
    <span class="abs main-nav" style="left:417px">HOME</span>
    <span class="abs main-nav" style="left:484px">ABOUT US</span>
    <span class="abs main-nav" style="left:578px">OUR SECURITY SOLUTIONS</span>
    <span class="abs main-nav" style="left:783px">INDUSTRIES WE SERVE</span>
    <span class="abs main-nav" style="left:962px">CONTACT US</span>
  </nav>
  <div class="abs social header-social"><span></span><span></span><span></span></div>
</header>

<section class="abs hero">
  <div class="abs hero-arrow" style="left:102px"><svg width="52" height="52"><path d="M29 17 L20 26 L29 35" fill="none" stroke="#fff" stroke-width="2"/></svg></div>
  <div class="abs hero-arrow" style="left:1046px"><svg width="52" height="52"><path d="M23 17 L32 26 L23 35" fill="none" stroke="#fff" stroke-width="2"/></svg></div>
  <div class="abs hero-photo" role="img" aria-label="Security camera mounted on a metal pole"></div>
  <h1 class="abs hero-title"><strong>Lorem Ipsum</strong> is simply dummy text of<br>the printing and typesetting industry.</h1>
</section>

<section class="abs solutions">
  <h2 class="abs head section-title" style="top:52px">Our Security Solutions</h2>
  <h3 class="abs head services-heading">Services</h3>
  <ul class="abs services-list">
    <li>Property guards</li>
    <li>Corporate events security</li>
    <li>Personal bodyguard for high net worth individuals</li>
    <li>Security consultancy</li>
    <li>Private investigation</li>
  </ul>
  <div class="abs custom-box">
    <div class="head">CUSTOM OPTIONS<br>AVAILABLE</div>
    <div class="box-name">TAVRON<br>Security Services Ltd.</div>
  </div>

  <div class="abs col-line" style="left:378px"></div>
  <div class="abs col-line" style="left:600px"></div>
  <div class="abs col-line" style="left:822px"></div>
  <div class="abs col-line" style="left:1044px"></div>
  <div class="abs row-line" style="left:378px;top:407px;width:222px"></div>
  <div class="abs row-line" style="left:600px;top:421px;width:222px"></div>
  <div class="abs row-line" style="left:822px;top:383px;width:222px"></div>

  <article class="abs card" style="left:378px;top:151px;width:222px;height:256px">
    <div class="card-img" role="img" aria-label="Model of a suburban house" style="background:linear-gradient(#8fa0b0,#9c6a4c)"></div>
    <h3 class="head">Property Guards</h3>
    <p>Lorem ipsum dolor sit amet, cons ectetuer adipiscing elit, sed diam nonummy nibh.</p>
    <span class="btn" style="top:204px">Read More</span>
  </article>
  <article class="abs card" style="left:600px;top:151px;width:222px;height:270px">
    <div class="card-img" role="img" aria-label="Bodyguard in a dark suit with arms crossed" style="background:linear-gradient(#3a4a6a,#141a28)"></div>
    <h3 class="head">Personal Bodyguards</h3>
    <p>Duis autem vel eum iriure dolor i n hendrerit in vulputate velit esse molestie consequat.</p>
    <span class="btn" style="top:222px">Read More</span>
  </article>
  <article class="abs card" style="left:822px;top:151px;width:222px;height:232px">
    <div class="card-img" role="img" aria-label="Investigator with a camera inside a car" style="background:linear-gradient(#a9b8c6,#4a525a)"></div>
    <h3 class="head">Private Investigation</h3>
    <p>Ut wisi enim ad minim veniam, qu is nostrud exerci tation ullamcorp er suscipit lobortis</p>
    <span class="btn" style="top:192px">Read More</span>
  </article>
  <article class="abs card" style="left:378px;top:407px;width:222px;height:305px">
    <div class="card-img" role="img" aria-label="Security staff in branded jackets at an event" style="background:linear-gradient(#5a6f8a,#1c222c)"></div>
    <h3 class="head">Corporate Events Security</h3>
    <p>Lorem ipsum dolor sit amet, cons ectetuer adipiscing elit, sed diam nonummy nibh euismod tincidunt ut laoreet dolore.</p>
    <span class="btn" style="top:230px">Read More</span>
  </article>
  <article class="abs card" style="left:600px;top:421px;width:222px;height:291px">
    <div class="card-img" role="img" aria-label="Business consultants shaking hands" style="background:linear-gradient(#c4c8cc,#3a3d42)"></div>
    <h3 class="head">Security Consultancy</h3>
    <p>Duis autem vel eum iriure dolor in hendrerit in vulputate velit ess e molestie consequat, vel illum d olore eu feugiat nulla.</p>
    <span class="btn" style="top:230px">Read More</span>
  </article>
  <article class="abs card" style="left:822px;top:383px;width:222px;height:329px">
    <div class="card-img" role="img" aria-label="Protection team beside a black vehicle" style="background:linear-gradient(#b5b7b9,#2a2c30)"></div>
    <h3 class="head">Executive Protection</h3>
    <p>Lorem ipsum dolor sit amet, cons ectetuer adipiscing elit, sed diam nonummy nibh euismod tincidunt ut laoreet dolore magna aliquam erat volutpat.</p>
    <span class="btn" style="top:242px">Read More</span>
  </article>
</section>

<section class="abs industries">
  <h2 class="abs head section-title" style="top:50px">Industries We Serve</h2>
  <div class="abs ind-arrow" style="left:108px"><svg width="36" height="36"><path d="M21 11 L14 18 L21 25" fill="none" stroke="#fff" stroke-width="1.6"/></svg></div>
  <div class="abs ind-arrow" style="left:1058px"><svg width="36" height="36"><path d="M15 11 L22 18 L15 25" fill="none" stroke="#fff" stroke-width="1.6"/></svg></div>
  <div class="abs ind-item" style="left:157px"><div class="ind-img" role="img" aria-label="National flag above a government building" style="background:linear-gradient(#5d86c9,#c6d3e2 60%,#6a6f72)"></div><div class="head">Government</div></div>
  <div class="abs ind-item" style="left:389px"><div class="ind-img" role="img" aria-label="Solar panels and wind turbines under blue sky" style="background:linear-gradient(#7fb7ea,#2d5fa8 60%,#1d3d73)"></div><div class="head">Energy and Environment</div></div>
  <div class="abs ind-item" style="left:618px"><div class="ind-img" role="img" aria-label="Oil pump silhouettes at sunset" style="background:linear-gradient(#e8782a,#b83d12 60%,#2a130a)"></div><div class="head">Oil and Gas</div></div>
  <div class="abs ind-item" style="left:848px"><div class="ind-img" role="img" aria-label="Cargo plane, truck and ship" style="background:linear-gradient(#fafafa,#cfcfcf 60%,#8c8c8c)"></div><div class="head">Transportation and Logistics</div></div>
</section>

<section class="abs split">
  <div class="abs split-divider"></div>
  <div class="abs split-col" style="left:118px">
    <div class="split-img" role="img" aria-label="Homeowner using an alarm keypad" style="background:linear-gradient(#c9b79a,#7a5c44)"></div>
    <div class="head">Residential Solutions</div>
    <p>Lorem ipsum dolor sit amet, consectetur adipiscing elit. Sed in porta ut mauris vitae accumsan. Ut bibendum condim Phasellus placerat lectus nec odio fermentum, non Proin nec ligula condimentum, aliquet nisi id,</p>
    <span class="btn">Read More</span>
  </div>
  <div class="abs split-col" style="left:659px">
    <div class="split-img" role="img" aria-label="Security guard in front of a glass office tower" style="background:linear-gradient(#8fb2d6,#1f2d44)"></div>
    <div class="head">Commercial Solutions</div>
    <p>Lorem ipsum dolor sit amet, consectetur adipiscing elit. Sed in porta ut mauris vitae accumsan. Ut bibendum condim Phasellus placerat lectus nec odio fermentum, non Proin nec ligula condimentum, aliquet nisi id,</p>
    <span class="btn">Read More</span>
  </div>
</section>

<footer class="abs site-footer">
  <h3 class="abs footer-title" style="left:157px">About us</h3>
  <h3 class="abs footer-title" style="left:541px">Quick Links</h3>
  <h3 class="abs footer-title" style="left:767px">Newsletter Signup</h3>
  <div class="abs about-text">
    <p>Lorem ipsum dolor sit amet, consectetur adipiscing elit. Morbi pellentesque iaculis justo eget fermentum. Pellentesque commodo iaculis neque, vitae tincidunt odio pellentesque luctus. Aenean in eros eu magna vestibulum imperdiet pretium nec augue.</p>
    <p>Etiam quis turpis enim. Vestibulum auctor id mauris vulputate consequat. Suspendisse potenti. Cras at imperdiet elit. Integer fringilla tellus non diam condimentum, sed ultricies urna ultricies. Sed cong dui quis dui convallis dictum. Donec malesuada vulputate risus vitae vulputate. Maecenas in congue urna. Sed porttitor bibendum.</p>
  </div>
  <ul class="abs quick-links">
    <li><svg width="8" height="10"><path d="M1 1 L6 5 L1 9" fill="none" stroke="#ddd" stroke-width="1.6"/></svg>HOME</li>
    <li><svg width="8" height="10"><path d="M1 1 L6 5 L1 9" fill="none" stroke="#ddd" stroke-width="1.6"/></svg>OUR SERVICES</li>
    <li><svg width="8" height="10"><path d="M1 1 L6 5 L1 9" fill="none" stroke="#ddd" stroke-width="1.6"/></svg>ABOUT</li>
    <li><svg width="8" height="10"><path d="M1 1 L6 5 L1 9" fill="none" stroke="#ddd" stroke-width="1.6"/></svg>LOCATIONS</li>
    <li><svg width="8" height="10"><path d="M1 1 L6 5 L1 9" fill="none" stroke="#ddd" stroke-width="1.6"/></svg>NEWS</li>
    <li><svg width="8" height="10"><path d="M1 1 L6 5 L1 9" fill="none" stroke="#ddd" stroke-width="1.6"/></svg>CAREERS</li>
    <li><svg width="8" height="10"><path d="M1 1 L6 5 L1 9" fill="none" stroke="#ddd" stroke-width="1.6"/></svg>CONTACT US</li>
  </ul>
  <p class="abs news-text">Fill the form below and recive our latest offers &amp; updates</p>
  <div class="abs field" style="top:193px">Your Name</div>
  <div class="abs field" style="top:240px">Your Email</div>
  <span class="abs btn" style="left:769px;top:293px;width:142px;text-align:center;padding:9px 0">Signup Now!</span>
  <div class="abs footer-rule"></div>
  <p class="abs copyright">Copyright © 2014 Tavron Security Services LTD.</p>
  <div class="abs social footer-social"><span></span><span></span><span></span></div>
</footer>

</body>
</html>
```